Kelo Wave Mint Business cards

Logo, tag line and photo on card
Agent Name
Title
Address
Phone number
Email
Website
Make logo on one side large by rotating  to portrait format.  Keep the background of the logo white.

Contact Information for Business Card
Slogan; Making Every Wave Count

```html
<!DOCTYPE html>
<html lang="en">
<head>
<meta charset="UTF-8">
<title>Kelo Wave Mint — Business Cards</title>
<link rel="stylesheet" href="https://fonts.googleapis.com/css2?family=Open+Sans:wght@400;600;800&display=swap">
<style>
  :root {
    --stage: #222222;
    --navy: #222f63;
    --navy-ink: #1f2a6b;
    --red: #c8232c;
    --coral: #f06a4a;
    --paper: #ffffff;
    --ink: #1b1b1b;
    --photo-light: #d9d9d9;
    --photo-dark: #4a4a4a;
  }
  * { box-sizing: border-box; margin: 0; padding: 0; }
  html, body {
    width: 1200px; height: 780px; overflow: hidden;
    background: var(--stage);
    font-family: "Open Sans", Arial, sans-serif;
  }
  .stage {
    width: 1200px; height: 780px;
    display: flex; align-items: center; justify-content: center; gap: 40px;
  }
  .card {
    position: relative;
    width: 540px; height: 310px;
    border-radius: 22px;
    overflow: hidden;
    box-shadow: 0 14px 30px rgba(0,0,0,.55);
  }

  /* Back side */
  .card--back { background: var(--navy); display: flex; align-items: center; justify-content: center; }
  .back-logo {
    width: 150px; height: 196px;
    border: 4px solid var(--coral);
    border-radius: 14px;
    display: flex; align-items: center; justify-content: center;
  }
  .back-logo__name {
    font-weight: 800; font-size: 34px; line-height: 1.1;
    color: #3c66c9; text-align: center;
  }

  /* Front side */
  .card--front { background: var(--paper); }
  .portrait {
    position: absolute; left: 60px; bottom: 0;
    width: 270px; height: 240px;
    background: radial-gradient(ellipse at 45% 30%, var(--photo-light) 0%, #9a9a9a 45%, var(--photo-dark) 100%);
    border-radius: 130px 130px 0 0;
  }
  .front-logo {
    position: absolute; top: 14px; right: 40px;
    width: 86px; height: 98px;
    border: 3px solid var(--red);
    border-radius: 8px;
    display: flex; align-items: center; justify-content: center;
  }
  .front-logo__name {
    font-weight: 800; font-size: 19px; line-height: 1.08;
    color: var(--navy-ink); text-align: center;
  }
  .name-bar {
    position: absolute; right: 0; top: 118px;
    width: 12px; height: 28px; background: var(--red);
  }
  .details {
    position: absolute; right: 24px; top: 116px;
    text-align: right; color: var(--ink);
  }
  .agent-name { font-weight: 800; font-size: 21px; line-height: 24px; }
  .agent-name__first { color: var(--red); }
  .agent-name__last { color: var(--navy-ink); }
  .agent-title { font-size: 11px; line-height: 14px; }
  .address { font-size: 11px; line-height: 14px; margin-top: 8px; }
  .contacts { list-style: none; margin-top: 8px; font-size: 11px; line-height: 16px; }
  .contacts li { display: flex; align-items: center; justify-content: flex-end; gap: 6px; }
  .contacts svg { width: 10px; height: 10px; fill: var(--red); flex: none; }
  .slogan {
    position: absolute; right: 24px; bottom: 14px;
    color: var(--red); font-size: 14px; line-height: 19px; font-weight: 600;
  }
</style>
</head>
<body>
<main class="stage">
  <section class="card card--back" aria-label="Card back">
    <div class="back-logo">
      <span class="back-logo__name">Kelo<br>Wave<br>Mint</span>
    </div>
  </section>

  <section class="card card--front" aria-label="Card front">
    <div class="portrait" role="img" aria-label="Portrait photo of the co-founder"></div>

    <div class="front-logo">
      <span class="front-logo__name">Kelo<br>Wave<br>Mint</span>
    </div>

    <div class="name-bar"></div>
    <div class="details">
      <h1 class="agent-name"><span class="agent-name__first">Daniel</span> <span class="agent-name__last">Brevik</span></h1>
      <p class="agent-title">Co-Founder</p>
      <p class="address">418 Harlow Ave. Suite 120<br>Millbrook, TX 75300</p>
      <ul class="contacts">
        <li>(555) 014-2290
          <svg viewBox="0 0 24 24" aria-hidden="true"><path d="M6.6 10.8a15 15 0 0 0 6.6 6.6l2.2-2.2a1 1 0 0 1 1-.25 11.4 11.4 0 0 0 3.6.57 1 1 0 0 1 1 1V20a1 1 0 0 1-1 1A17 17 0 0 1 3 4a1 1 0 0 1 1-1h3.5a1 1 0 0 1 1 1 11.4 11.4 0 0 0 .57 3.6 1 1 0 0 1-.25 1z"/></svg>
        </li>
        <li>hello@kelowavemint.com
          <svg viewBox="0 0 24 24" aria-hidden="true"><path d="M2 5h20v14H2zm2 2v.5l8 5 8-5V7z"/></svg>
        </li>
        <li>www.kelowavemint.com
          <svg viewBox="0 0 24 24" aria-hidden="true"><circle cx="12" cy="12" r="10"/></svg>
        </li>
      </ul>
    </div>
    <p class="slogan">Making Every Wave Count</p>
  </section>
</main>
</body>
</html>
```